Business Card Design

We like to use greens as you will see in our logo (but not TOO much green). We are a Dental Clinic in a somewhat eccentric community. We do not like the dated sharp designs which we see many dentists use. We're looking for something bright and fresh while still maintaining the integrity of the profession. Elegance is not necessarily what we are going for... we need for the design to be "mature" but also up-lifting.

See our logo.
Updates

Project Deadline Extended
Reason: We have 5 designs which we like. But we'd like to see a few more before committing to a design.

Project Deadline Extended
Reason: We are awaiting revisions to this project. We are still welcoming designs while we wait to see if designers are able to provide to us the revisions we require in order to proceed with a selection.

Target Market(s)

Younger families - ages late 20's to early 40's

Industry/Entity Type

Business

Contact Information for Business Card

Corwel T. Banfry DDS 2730 W. Halvert Rd. Ste. 7 Fernhollow, OR 48391 (503)555-0174 FX (503)555-0189 info@BrightwellDentalCareMi.com BrigthwellDentalCareMi.com on the back of the card we need an appointment reminder (For____ Date___ Time____) with "If you are unable to keep your appointment, kindly give 48 hours notice" at the bottom. No use of teeth in the design. DOUBLE SIDED DESIGN

Requirements
Should not have
• The use of pictures of teeth

```html
<!DOCTYPE html>
<html lang="en">
<head>
<meta charset="utf-8">
<title>Brightwell Dental Care – Business Card</title>
<link rel="stylesheet" href="https://fonts.googleapis.com/css2?family=Open+Sans:ital,wght@0,400;0,600;0,700;1,400&family=Cinzel:wght@400&display=swap">
<style>
  :root {
    --backdrop: #e9e6e1;
    --card: #ffffff;
    --card-edge: #3c3c3c;
    --brand-green: #1f6b35;
    --leaf-green: #8cc63f;
    --ink: #1c1c1c;
    --field-line: #555555;
    --icon: #2e6b3a;
  }
  * { box-sizing: border-box; margin: 0; padding: 0; }
  html, body { width: 1200px; height: 1184px; overflow: hidden; }
  body {
    background: var(--backdrop);
    font-family: "Open Sans", Arial, sans-serif;
    color: var(--ink);
    position: relative;
  }
  .card {
    position: absolute;
    width: 941px;
    height: 538px;
    background: var(--card);
    border: 1.5px solid var(--card-edge);
  }
  .card--front { left: 200px; top: 29px; }
  .card--back { left: 36px; top: 612px; }

  /* Front */
  .brand {
    position: absolute;
    left: 40px;
    top: 92px;
    display: flex;
    align-items: center;
    gap: 18px;
  }
  .brand__dot {
    width: 40px; height: 40px; border-radius: 50%;
    background: var(--leaf-green);
    flex: none;
  }
  .brand__name {
    font-weight: 600;
    font-size: 58px;
    color: var(--brand-green);
    line-height: 66px;
  }
  .contact-list {
    position: absolute;
    left: 40px;
    top: 292px;
    list-style: none;
    font-size: 23px;
  }
  .contact-list li {
    display: flex;
    align-items: center;
    gap: 8px;
    height: 41px;
  }
  .contact-list svg { width: 18px; height: 18px; flex: none; }
  .address {
    position: absolute;
    left: 40px;
    top: 460px;
    font-size: 23px;
    line-height: 30px;
  }
  .practitioner {
    position: absolute;
    right: 205px;
    top: 448px;
    text-align: right;
  }
  .practitioner__name {
    font-weight: 700;
    font-size: 32px;
    color: var(--brand-green);
    line-height: 40px;
  }
  .practitioner__title { font-size: 24px; line-height: 32px; }

  /* Back */
  .appointment__title {
    position: absolute;
    left: 0; right: 0;
    top: 92px;
    text-align: center;
    font-family: "Cinzel", Georgia, serif;
    font-weight: 400;
    font-size: 36px;
    color: var(--brand-green);
    letter-spacing: 1px;
  }
  .field-label {
    position: absolute;
    font-size: 24px;
    line-height: 30px;
  }
  .field-line {
    position: absolute;
    border-bottom: 2px dotted var(--field-line);
    height: 0;
  }
  .slot {
    position: absolute;
    border: 1.5px solid var(--field-line);
    border-radius: 4px;
  }
  .day {
    position: absolute;
    font-size: 25px;
    font-weight: 600;
    line-height: 30px;
  }
  .notice {
    position: absolute;
    left: 0; right: 0;
    top: 460px;
    text-align: center;
    font-style: italic;
    font-size: 24px;
  }
</style>
</head>
<body>

<section class="card card--front" aria-label="Business card front">
  <div class="brand">
    <span class="brand__dot"></span>
    <span class="brand__name">Brightwell<br>Dental Care</span>
  </div>

  <ul class="contact-list">
    <li>
      <svg viewBox="0 0 20 20" aria-hidden="true"><circle cx="10" cy="10" r="9" fill="none" stroke="var(--icon)" stroke-width="1.6"/><path d="M7 5l2 2-1 2 3 3 2-1 2 2-2 2c-4 0-8-4-8-8z" fill="var(--icon)"/></svg>
      (503)555-0174
    </li>
    <li>
      <svg viewBox="0 0 20 20" aria-hidden="true"><rect x="2" y="8" width="16" height="8" rx="2" fill="var(--icon)"/><rect x="5" y="3" width="10" height="6" fill="none" stroke="var(--icon)" stroke-width="1.6"/></svg>
      (503)555-0189
    </li>
    <li>
      <svg viewBox="0 0 20 20" aria-hidden="true"><rect x="2" y="4" width="16" height="12" rx="1.5" fill="var(--icon)"/><path d="M2 5l8 6 8-6" fill="none" stroke="#fff" stroke-width="1.5"/></svg>
      info@BrightwellDentalCareMi.com
    </li>
    <li>
      <svg viewBox="0 0 20 20" aria-hidden="true"><circle cx="10" cy="10" r="8.5" fill="none" stroke="var(--icon)" stroke-width="1.6"/><ellipse cx="10" cy="10" rx="3.5" ry="8.5" fill="none" stroke="var(--icon)" stroke-width="1.3"/><path d="M2 10h16" stroke="var(--icon)" stroke-width="1.3"/></svg>
      BrigthwellDentalCareMi.com
    </li>
  </ul>

  <p class="address">2730 W. Halvert Rd.<br>Ste. 7 Fernhollow, OR 48391</p>

  <div class="practitioner">
    <p class="practitioner__name">Corwel T. Banfry</p>
    <p class="practitioner__title">DDS</p>
  </div>
</section>

<section class="card card--back" aria-label="Appointment reminder card">
  <h1 class="appointment__title">YOUR APPOINTMENT</h1>

  <span class="field-label" style="left:72px; top:161px;">Name :</span>
  <span class="field-line" style="left:179px; width:684px; top:183px;"></span>

  <span class="field-label" style="left:72px; top:226px;">Date :</span>
  <span class="field-line" style="left:179px; width:228px; top:248px;"></span>
  <span class="field-label" style="left:423px; top:226px;">Time :</span>
  <span class="field-line" style="left:506px; width:248px; top:248px;"></span>
  <span class="field-label" style="left:760px; top:226px;">am / pm</span>

  <span class="field-label" style="left:72px; top:294px;">Next Appointment</span>
  <span class="slot" style="left:334px; top:291px; width:167px; height:38px;"></span>
  <span class="slot" style="left:516px; top:291px; width:169px; height:38px;"></span>
  <span class="slot" style="left:695px; top:291px; width:169px; height:38px;"></span>

  <span class="day" style="left:70px; top:384px;">MON</span>
  <span class="slot" style="left:146px; top:383px; width:59px; height:36px;"></span>
  <span class="day" style="left:216px; top:384px;">TUE</span>
  <span class="slot" style="left:278px; top:383px; width:59px; height:36px;"></span>
  <span class="day" style="left:350px; top:384px;">WED</span>
  <span class="slot" style="left:423px; top:383px; width:59px; height:36px;"></span>
  <span class="day" style="left:493px; top:384px;">THU</span>
  <span class="slot" style="left:560px; top:383px; width:58px; height:36px;"></span>
  <span class="day" style="left:630px; top:384px;">FRI</span>
  <span class="slot" style="left:682px; top:383px; width:59px; height:36px;"></span>
  <span class="day" style="left:752px; top:384px;">SAT</span>
  <span class="slot" style="left:812px; top:383px; width:57px; height:36px;"></span>

  <p class="notice">If you are unable to keep your appointment, kindly give 48 hours notice</p>
</section>

</body>
</html>
```